Home Remodeling company needs a business card design

we need a business card design for home remodeling company in hamilton county, indiana USA. we offers a wide range of construction services including whole house renovations, Design and Build Basements and Kitchen and Bathroom Remodeling . we would like to see designs for both site of business card that use the same color of the company logo and also including all information below :
1- Karim Feltous CEO / General Contractor
2- all company contacts Telephone numbers ( 1-888-DULOM-47 ) ( 317-555-0193) email address ( info@dulomhome.com) website ( www.dulomhome.com ) and social media logos (Facebook- twitter- google plus )
3- company logo
4- licensed . insured . bonded

```html
<!DOCTYPE html>
<html lang="en">
<head>
<meta charset="utf-8">
<title>Dulom Home Remodeling – Business Card</title>
<link rel="stylesheet" href="https://fonts.googleapis.com/css2?family=Lato:wght@400;700&family=Michroma&display=swap">
<style>
  :root {
    --backdrop: #8e8e8e;
    --card-white: #f1f1f2;
    --ink-dark: #2b2b2f;
    --ink-grey: #5a5a60;
    --brand-red: #a82a32;
    --paper-light: #ebebeb;
  }
  * { box-sizing: border-box; margin: 0; padding: 0; }
  html, body {
    width: 1105px;
    height: 1200px;
    overflow: hidden;
    background: var(--backdrop);
    font-family: "Lato", sans-serif;
  }
  .canvas { position: relative; width: 1105px; height: 1200px; }

  .card {
    position: absolute;
    left: 182px;
    width: 747px;
    height: 425px;
  }
  .card-front { top: 119px; background: var(--card-white); }
  .card-back  { top: 637px; background: var(--brand-red); }

  /* Front: brand block */
  .brand {
    position: absolute;
    top: 134px;
    left: 0;
    width: 100%;
    text-align: center;
  }
  .brand-line {
    display: inline-flex;
    align-items: center;
    gap: 12px;
  }
  .brand-square {
    width: 14px;
    height: 14px;
    background: var(--brand-red);
  }
  .brand-name {
    font-family: "Michroma", sans-serif;
    font-size: 56px;
    line-height: 1;
    color: var(--ink-dark);
    letter-spacing: 3px;
  }
  .brand-tagline {
    margin-top: 12px;
    font-size: 20px;
    letter-spacing: 6.5px;
    color: var(--ink-grey);
    padding-left: 20px;
  }

  /* Front: contact row */
  .contact-row {
    position: absolute;
    top: 334px;
    left: 40px;
    display: flex;
    align-items: center;
  }
  .person-name {
    font-size: 27px;
    font-weight: 700;
    color: var(--ink-dark);
    line-height: 1.1;
  }
  .person-title {
    font-size: 17px;
    color: var(--brand-red);
    margin-top: 4px;
  }
  .divider {
    width: 1px;
    height: 54px;
    background: #9a9a9e;
    margin: 0 16px;
  }
  .contact-list { list-style: none; }
  .contact-list li {
    display: flex;
    align-items: center;
    gap: 8px;
    font-size: 19px;
    color: var(--ink-dark);
    line-height: 30px;
  }
  .contact-list svg { width: 17px; height: 17px; fill: var(--ink-dark); flex: none; }

  /* Back */
  .back-name {
    position: absolute;
    top: 140px;
    width: 100%;
    text-align: center;
    font-family: "Michroma", sans-serif;
    font-size: 64px;
    letter-spacing: 4px;
    color: var(--paper-light);
  }
  .credentials {
    position: absolute;
    top: 318px;
    width: 100%;
    text-align: center;
    font-size: 21px;
    color: var(--paper-light);
    letter-spacing: 0.5px;
  }
  .social-row {
    position: absolute;
    top: 362px;
    left: 0;
    width: 100%;
    display: flex;
    justify-content: center;
    align-items: center;
    gap: 6px;
  }
  .social-rule { width: 70px; height: 1px; background: rgba(235,235,235,0.6); }
  .social-dot { width: 24px; height: 24px; border-radius: 50%; background: var(--paper-light); }
</style>
</head>
<body>
<main class="canvas">

  <section class="card card-front">
    <div class="brand">
      <div class="brand-line">
        <span class="brand-square"></span>
        <span class="brand-name">DULOM</span>
      </div>
      <div class="brand-tagline">HOME REMODELING</div>
    </div>

    <div class="contact-row">
      <div class="person">
        <div class="person-name">Karim Feltous</div>
        <div class="person-title">CEO / General Contractor</div>
      </div>
      <span class="divider"></span>
      <ul class="contact-list">
        <li>
          <svg viewBox="0 0 24 24" aria-hidden="true"><path d="M6.6 10.8a15.1 15.1 0 0 0 6.6 6.6l2.2-2.2a1 1 0 0 1 1-.25 11.4 11.4 0 0 0 3.6.57 1 1 0 0 1 1 1V20a1 1 0 0 1-1 1A17 17 0 0 1 3 4a1 1 0 0 1 1-1h3.5a1 1 0 0 1 1 1c0 1.25.2 2.45.57 3.57a1 1 0 0 1-.25 1z"/></svg>
          1-888-DULOM-47
        </li>
        <li>
          <svg viewBox="0 0 24 24" aria-hidden="true"><path d="M7 1h10a2 2 0 0 1 2 2v18a2 2 0 0 1-2 2H7a2 2 0 0 1-2-2V3a2 2 0 0 1 2-2zm0 3v14h10V4zm5 15.5a1 1 0 1 0 0 2 1 1 0 0 0 0-2z"/></svg>
          317-555-0193
        </li>
      </ul>
      <span class="divider"></span>
      <ul class="contact-list">
        <li>
          <svg viewBox="0 0 24 24" aria-hidden="true"><path d="M2 5h20v14H2zm2 2v.4l8 5 8-5V7zm0 2.8V17h16V9.8l-8 5z"/></svg>
          info@dulomhome.com
        </li>
        <li>
          <svg viewBox="0 0 24 24" aria-hidden="true"><path d="M12 2a10 10 0 1 0 0 20 10 10 0 0 0 0-20zm6.9 6h-3a15 15 0 0 0-1.3-3.7A8 8 0 0 1 18.9 8zM12 4c.8 1.1 1.5 2.5 1.9 4h-3.8c.4-1.5 1.1-2.9 1.9-4zM4.3 14a8 8 0 0 1 0-4h3.4a16 16 0 0 0 0 4zm.8 2h3a15 15 0 0 0 1.3 3.7A8 8 0 0 1 5.1 16zm3-8h-3a8 8 0 0 1 4.3-3.7A15 15 0 0 0 8.1 8zM12 20c-.8-1.1-1.5-2.5-1.9-4h3.8c-.4 1.5-1.1 2.9-1.9 4zm2.3-6H9.7a14 14 0 0 1 0-4h4.6a14 14 0 0 1 0 4zm.3 5.7a15 15 0 0 0 1.3-3.7h3a8 8 0 0 1-4.3 3.7zm1.7-5.7a16 16 0 0 0 0-4h3.4a8 8 0 0 1 0 4z"/></svg>
          www.dulomhome.com
        </li>
      </ul>
    </div>
  </section>

  <section class="card card-back">
    <div class="back-name">DULOM</div>
    <div class="credentials">LICENSED | INSURED | BONDED</div>
    <div class="social-row">
      <span class="social-rule"></span>
      <span class="social-dot"></span>
      <span class="social-dot"></span>
      <span class="social-dot"></span>
      <span class="social-rule"></span>
    </div>
  </section>

</main>
</body>
</html>
```